Marwick Law Letterhead

We need a new letterhead design for a Law Firm. The address for the law firm is 1475 Calloway Street, Suite 210, Houston, Texas 77041. Phone Number: 832-361-9027; Fax Number: 832-614-7359. The logo is uploaded to the project.

```html
<!DOCTYPE html>
<html lang="en">
<head>
<meta charset="utf-8">
<title>Marwick Law Letterhead</title>
<link rel="stylesheet" href="https://fonts.googleapis.com/css2?family=Arimo:wght@400;700&family=Libre+Baskerville:wght@400;700&display=swap">
<style>
  :root {
    --backdrop: #e7e4e0;
    --paper: #ffffff;
    --header-grey: #f2f2f2;
    --navy: #1c2d5a;
    --navy-deep: #142347;
    --navy-bright: #2a4487;
    --accent-red: #d3282f;
    --ink: #1a1a1a;
    --signature-tone: #e3e3e6;
  }
  * { box-sizing: border-box; margin: 0; padding: 0; }
  html, body {
    width: 1200px; height: 900px; overflow: hidden;
    background: var(--backdrop);
  }
  .letterhead {
    position: absolute; left: 268px; top: 20px;
    width: 665px; height: 860px;
    background: var(--paper);
    box-shadow: 0 4px 18px rgba(0,0,0,0.18);
    font-family: "Arimo", Arial, sans-serif;
    color: var(--ink);
  }
  .letterhead-header {
    height: 118px; background: var(--header-grey);
    display: flex; align-items: center; padding-left: 73px;
  }
  .brand { display: flex; align-items: center; gap: 12px; }
  .brand-square { width: 22px; height: 22px; background: var(--navy); }
  .brand-name {
    font-family: "Libre Baskerville", Georgia, serif;
    font-weight: 400; font-size: 30px; color: var(--navy);
    letter-spacing: 0.5px;
  }
  .letter-body {
    position: absolute; left: 69px; right: 67px; top: 155px;
    font-size: 12.6px; line-height: 20.5px;
  }
  .letter-date { margin-bottom: 33px; }
  .recipient { margin-bottom: 40px; }
  .recipient-name { font-weight: 700; font-size: 14px; }
  .letter-text p { text-align: justify; margin-bottom: 20.5px; }
  .letter-text p.tight { margin-bottom: 0; }
  .closing { margin-top: 0; }
  .signature {
    width: 86px; height: 22px; margin-top: 38px;
    background: linear-gradient(90deg, var(--signature-tone), #f2f2f4);
    border-radius: 3px;
  }
  .signer-name { font-size: 15.5px; margin-top: 11px; }
  .contact-strip {
    position: absolute; left: 74px; right: 70px; top: 813px;
    display: flex; justify-content: space-between; align-items: center;
    font-family: "Libre Baskerville", Georgia, serif;
    font-weight: 700; font-size: 8.6px; color: var(--navy);
    letter-spacing: 0.6px;
  }
  .contact-item { display: flex; align-items: center; gap: 5px; white-space: nowrap; }
  .contact-icon { width: 10px; height: 10px; fill: var(--accent-red); }
  .footer-band { position: absolute; left: 0; bottom: 4px; width: 665px; height: 10px; }
</style>
</head>
<body>
  <article class="letterhead">
    <header class="letterhead-header">
      <div class="brand">
        <span class="brand-square"></span>
        <span class="brand-name">Marwick Law</span>
      </div>
    </header>

    <section class="letter-body">
      <p class="letter-date">4th September 20XX</p>
      <div class="recipient">
        <p class="recipient-name">Ronny Reader</p>
        <p>CEO, Company Name</p>
        <p>123 Address St</p>
        <p>Anytown, ST 12345</p>
      </div>
      <div class="letter-text">
        <p class="tight">Dear Mr. Reader,</p>
        <p>Lorem ipsum dolor sit amet, consectetuer adipiscing elit, sed diam nonummy nibh euismod tincidunt ut laoreet dolore magna aliquam erat volutpat. Ut wisi enim ad minim veniam, quis nostrud exerci tation ullamcorper suscipit lobortis nisl ut aliquip ex ea commodo consequat.</p>
        <p>Duis autem vel eum iriure dolor in hendrerit in vulputate velit esse molestie consequat, vel illum dolore eu feugiat nulla facilisis at vero eros et accumsan.</p>
        <p class="tight">Nam liber tempor cum soluta nobis eleifend option congue nihil imperdiet doming id quod mazim placerat facer possim assum. Typi non habent claritatem insitam; est usus legentis in iis qui facit eorum claritatem. Investigationes demonstraverunt lectores legere me lius quod ii legunt saepius.</p>
        <p class="closing">Sincerely,</p>
      </div>
      <div class="signature" role="img" aria-label="Handwritten signature of the sender"></div>
      <p class="signer-name">Your Name</p>
    </section>

    <footer class="contact-strip">
      <span class="contact-item">
        <svg class="contact-icon" viewBox="0 0 10 10"><circle cx="5" cy="5" r="5"/><circle cx="5" cy="4.3" r="1.5" fill="#fff"/></svg>
        1475 Calloway Street, Suite 210, Houston, Texas 77041
      </span>
      <span class="contact-item">
        <svg class="contact-icon" viewBox="0 0 10 10"><path d="M2.2 0.6 L3.6 2.6 L2.8 3.7 C3.4 5 4.9 6.6 6.3 7.2 L7.4 6.4 L9.4 7.8 L8.4 9.5 C4.5 9.2 0.8 5.5 0.5 1.6 Z"/></svg>
        832-361-9027
      </span>
      <span class="contact-item">
        <svg class="contact-icon" viewBox="0 0 10 10"><rect x="2.5" y="0.5" width="5" height="3"/><rect x="0.5" y="3.5" width="9" height="5" rx="1"/><rect x="2.5" y="5.5" width="5" height="1.4" fill="#fff"/></svg>
        832-614-7359
      </span>
    </footer>

    <svg class="footer-band" viewBox="0 0 665 10" preserveAspectRatio="none">
      <polygon points="0,0 334,0 324,10 0,10" fill="var(--navy-deep)"/>
      <polygon points="347,0 665,0 665,10 337,10" fill="var(--navy-bright)"/>
    </svg>
  </article>
</body>
</html>
```